QVR business card

Need a business card for a company that provides instructional design and elearning development services. The website is here: http://quorvane.studio/

I'm attaching a current logo, as well as the old business card design. While I like to keep it clean, the old design is too simplistic for my liking. The only idea I want to reuse from the old design is placing industry jargon on the back of the card, just need a better way to present it. But if you have other ideas for the back--feel free to experiment.

Please use the colors complementary to the color we have on the website. Thank you!

```html
<!DOCTYPE html>
<html lang="en">
<head>
<meta charset="utf-8">
<title>QVR business card</title>
<link rel="stylesheet" href="https://fonts.googleapis.com/css2?family=Open+Sans:wght@400;600;700;800&family=Fira+Sans+Condensed:wght@400&display=swap">
<style>
  :root {
    --backdrop: #2b2b2e;
    --teal: #1eb3b2;
    --teal-deep: #169c9b;
    --gold: #d4c38c;
    --white: #ffffff;
    --ink: #2d2d2d;
    --line: rgba(255,255,255,0.55);
  }
  * { box-sizing: border-box; margin: 0; padding: 0; }
  html, body { width: 1200px; height: 925px; overflow: hidden; }
  body {
    background: var(--backdrop);
    font-family: "Open Sans", Arial, sans-serif;
    display: flex; align-items: center; justify-content: center; gap: 20px;
  }
  .card {
    position: relative; width: 570px; height: 326px;
    border-radius: 4px; overflow: hidden;
    box-shadow: 0 12px 30px rgba(0,0,0,0.45);
  }

  /* Back: jargon */
  .card-back { background: var(--teal); color: var(--white); }
  .headline {
    position: absolute; left: 26px; top: 26px;
    font-weight: 800; line-height: 0.95; letter-spacing: 1px;
  }
  .headline span { display: block; font-size: 62px; }
  .headline .big { font-size: 92px; }
  .divider {
    position: absolute; left: 238px; top: 30px; bottom: 30px;
    width: 1px; background: var(--line);
  }
  .jargon {
    position: absolute; left: 256px; top: 30px; list-style: none;
    font-family: "Fira Sans Condensed", "Arial Narrow", sans-serif;
    font-size: 26px; line-height: 44px; text-transform: uppercase;
    white-space: nowrap;
  }

  /* Front: identity */
  .card-front { background: var(--teal); }
  .card-front svg.shape { position: absolute; inset: 0; }
  .wordmark {
    position: absolute; left: 72px; top: 134px;
    display: flex; align-items: center; gap: 12px;
    font-weight: 700; font-size: 44px; color: var(--teal); letter-spacing: 2px;
  }
  .wordmark .dot { width: 18px; height: 18px; border-radius: 50%; background: var(--gold); }
  .contact {
    position: absolute; right: 30px; top: 40px; text-align: right; color: var(--white);
  }
  .contact .name { font-weight: 700; font-size: 15px; letter-spacing: 1px; text-transform: uppercase; }
  .contact .role { font-size: 13px; color: #1d4f4f; margin-top: 2px; }
  .contact ul { list-style: none; margin-top: 90px; }
  .contact li {
    display: flex; justify-content: flex-end; align-items: center; gap: 8px;
    font-size: 13.5px; line-height: 26px;
  }
  .contact li svg { width: 16px; height: 16px; flex: none; }
</style>
</head>
<body>

<section class="card card-back">
  <h1 class="headline">
    <span>HOW</span>
    <span>CAN</span>
    <span class="big">WE</span>
    <span>HELP?</span>
  </h1>
  <div class="divider"></div>
  <ul class="jargon">
    <li>Mobile Learning SCORM</li>
    <li>Instructional Design LMS</li>
    <li>MOOCs eLearning HTML5</li>
    <li>Adult Learning Theory</li>
    <li>Gamification Classroom</li>
    <li>xAPI Blended Learning</li>
  </ul>
</section>

<section class="card card-front">
  <svg class="shape" width="570" height="326" viewBox="0 0 570 326">
    <polygon points="0,0 250,0 345,163 250,326 0,326" fill="#ffffff"/>
    <polyline points="250,0 345,163 250,326" fill="none" stroke="#d4c38c" stroke-width="4"/>
  </svg>
  <div class="wordmark"><span class="dot"></span>QVR</div>
  <div class="contact">
    <p class="name">Marcus Velden</p>
    <p class="role">Managing Director</p>
    <ul>
      <li>555-013-4827
        <svg viewBox="0 0 16 16"><circle cx="8" cy="8" r="8" fill="#d4c38c"/><path d="M5.2 4.2l1.6-.4.9 2-1 .8a5 5 0 0 0 2.7 2.7l.8-1 2 .9-.4 1.6c-3.6.2-6.8-3-6.6-6.6z" fill="#ffffff"/></svg>
      </li>
      <li>mvelden@quorvane.studio
        <svg viewBox="0 0 16 16"><circle cx="8" cy="8" r="8" fill="#d4c38c"/><rect x="4" y="5.2" width="8" height="5.6" rx="0.6" fill="none" stroke="#ffffff" stroke-width="1.1"/><path d="M4.3 5.6L8 8.4l3.7-2.8" fill="none" stroke="#ffffff" stroke-width="1.1"/></svg>
      </li>
      <li>www.quorvane.studio
        <svg viewBox="0 0 16 16"><circle cx="8" cy="8" r="8" fill="#d4c38c"/><circle cx="8" cy="8" r="4" fill="none" stroke="#ffffff" stroke-width="1"/><path d="M4 8h8M8 4c-2 2.2-2 5.8 0 8M8 4c2 2.2 2 5.8 0 8" fill="none" stroke="#ffffff" stroke-width="1"/></svg>
      </li>
    </ul>
  </div>
</section>

</body>
</html>
```